Design a Website for an IT Support Company

We are an IT support company that provides commercial IT support and services to small and medium sized businesses. We are in need of a website to be developed for our business.
We would like to work with someone who is either familiar with the IT field, or has developed a website for an IT support company in the past.
Some examples of designs/layouts that we like:
https://www.veldaworks.example/
http://www.marsbyquill.example/
http://817kq.example/
http://www.olbenstructures.example/
http://www.bykq.example/
I have attached a word document that gives a menu system/page layout format that we would like for our website as well as branch office phone numbers. Our logo is also attached that you can use for your design purposes. We currently do not have copy produced for all of the pages outlined in the word document, but would get this done during the project with the selected designer.
We would like the website to be SEO friendly & fully responsive. We would prefer a Wordpress format, however, we are open to HTML formats as well.

```html
<!DOCTYPE html>
<html lang="en">
<head>
<meta charset="utf-8">
<title>Brisk IT – Commercial IT Support</title>
<link href="https://fonts.googleapis.com/css2?family=Exo+2:wght@500;600&family=Poppins:wght@400;500&family=Arimo:wght@400;700&display=swap" rel="stylesheet">
<style>
:root{
  --blue:#1b6cb4;
  --blue-mid:#2e73b8;
  --blue-light:#5ab3e6;
  --navy:#13243c;
  --ink:#555c66;
  --pale:#f3f5f8;
  --footer:#2f72b6;
  --footer-dark:#3c3c3c;
  --white:#fff;
  --star:#e8b923;
}
*{margin:0;padding:0;box-sizing:border-box}
html,body{width:673px;height:1200px;overflow:hidden;background:var(--white)}
body{position:relative;font-family:"Arimo",Arial,sans-serif;color:var(--ink)}
.abs{position:absolute}
.heading{font-family:"Exo 2",sans-serif;font-weight:600;color:var(--blue);letter-spacing:.5px}
.body-text{font-size:6.6px;line-height:14.4px;color:var(--ink)}

/* header */
.topbar{left:366px;top:0;width:258px;height:24px;background:var(--blue-mid);clip-path:polygon(0 0,100% 0,97% 100%,3% 100%);color:#fff;font-family:"Poppins",sans-serif;font-size:8px;display:flex;align-items:center;justify-content:space-around;padding:0 12px}
.logo{display:flex;align-items:center;gap:6px}
.logo-dot{width:22px;height:22px;border-radius:50%;background:var(--blue-mid)}
.logo-name{font-family:"Exo 2",sans-serif;font-weight:600;font-size:20px;color:var(--navy)}
.nav{top:40px;font-family:"Poppins",sans-serif;font-size:6.5px;font-weight:500;color:#444}
.nav.active{color:var(--blue-mid)}
.nav-underline{left:316px;top:58px;width:29px;height:3px;background:var(--blue-mid)}
.search{left:604px;top:34px;width:20px;height:20px;border-radius:50%;background:var(--blue-mid)}

/* hero */
.hero{left:0;top:61px;width:673px;height:305px;background:linear-gradient(100deg,#14253f 0%,#1c3a63 55%,#24507f 100%)}
.hero-photo{left:340px;top:61px;width:333px;height:305px;background:radial-gradient(circle at 55% 45%,#4b78a8 0%,#24466f 45%,rgba(20,37,63,0) 80%)}
.hero h1{font-family:"Exo 2",sans-serif;font-weight:600;font-size:27px;color:#fff;left:48px;top:152px;letter-spacing:.5px}
.hero-sub{left:48px;top:191px;font-family:"Poppins",sans-serif;font-size:11.5px;color:var(--blue-light)}
.hero-text{left:49px;top:214px;width:270px;font-size:6.6px;line-height:14.4px;color:#e6edf5}
.btn-outline{left:49px;top:274px;width:97px;height:30px;border:1px solid var(--blue-light);border-radius:15px;color:var(--blue-light);font-family:"Poppins",sans-serif;font-size:9px;display:flex;align-items:center;justify-content:center}
.dots{left:49px;top:342px;display:flex;gap:2px}
.dots span{width:7px;height:7px;border-radius:50%;border:1px solid #fff}
.dots span.on{border-color:var(--blue-light)}

/* sections */
.section-title{width:673px;text-align:center;font-size:14px}
.section-sub{width:673px;text-align:center;font-size:6.6px;color:var(--ink)}
.service{width:170px;text-align:center}
.service-icon{width:64px;height:64px;border-radius:50%;background:var(--blue);margin:0 auto;display:flex;align-items:center;justify-content:center}
.service h3{font-size:10px;margin-top:9px}
.service p{margin-top:4px}

.why-bg{left:0;top:600px;width:362px;height:219px;background:var(--pale)}
.why-photo{left:362px;top:600px;width:311px;height:219px;background:linear-gradient(120deg,#dfe9f2 0%,#c9d6e2 45%,#a9bccd 100%)}
.btn-solid{left:48px;top:777px;width:73px;height:24px;background:var(--blue);color:#fff;font-family:"Exo 2",sans-serif;font-weight:600;font-size:8px;display:flex;align-items:center;justify-content:center}

.testimonial{width:190px;height:100px}
.avatar{position:absolute;left:0;top:0;width:48px;height:48px;border-radius:50%;background:linear-gradient(160deg,#c9b4a2,#8a7060);border:2px solid #ddd}
.quote{position:absolute;left:61px;top:0;width:128px;font-size:6.6px;line-height:12px}
.quote b{color:#999;font-size:9px;margin-right:3px}
.t-name{position:absolute;left:61px;top:59px;font-size:7px;font-weight:700;color:var(--blue)}
.t-date{position:absolute;left:61px;top:71px;font-size:6px}
.stars{position:absolute;left:61px;top:80px;color:var(--star);font-size:7px;letter-spacing:1px}

/* footer */
.footer{left:0;top:1026px;width:673px;height:137px;background:var(--footer);color:#fff}
.footer .logo-name{color:#fff;font-size:22px}
.footer .logo-dot{background:#fff;width:26px;height:26px}
.f-title{font-family:"Arimo",sans-serif;font-weight:700;font-size:9.5px;color:#fff}
.f-list{font-size:6.6px;line-height:13px;color:#fff}
.f-list td{padding-right:6px}
.input{left:359px;top:1108px;width:133px;height:19px;background:#fff;font-size:6.6px;color:#888;padding:6px 9px}
.subscribe{left:359px;top:1132px;width:45px;height:15px;background:#1d4e86;font-size:6px;color:#fff;display:flex;align-items:center;justify-content:center}
.social{left:507px;top:1121px;display:flex;gap:4px}
.social span{width:20px;height:20px;border-radius:50%;border:1px solid #fff}
.copyright{left:0;top:1163px;width:673px;height:37px;background:var(--footer-dark);color:#eee;font-size:7px;display:flex;align-items:center;justify-content:center}
</style>
</head>
<body>

<header>
  <div class="abs topbar"><span>☎ Call Us : 555-010-4400</span><span>✉ Email :info@briskit.example</span></div>
  <div class="abs logo" style="left:48px;top:22px"><span class="logo-dot"></span><span class="logo-name">Brisk IT</span></div>
  <nav>
    <span class="abs nav active" style="left:318px">HOME</span>
    <span class="abs nav" style="left:378px">ABOUT US</span>
    <span class="abs nav" style="left:452px">WHY BRISK IT</span>
    <span class="abs nav" style="left:551px">CONTACT US</span>
    <span class="abs nav-underline"></span>
    <span class="abs search"><svg width="20" height="20" viewBox="0 0 20 20"><circle cx="9" cy="9" r="3" fill="none" stroke="#fff" stroke-width="1.3"/><line x1="11.2" y1="11.2" x2="13.5" y2="13.5" stroke="#fff" stroke-width="1.3"/></svg></span>
  </nav>
</header>

<section class="hero-wrap">
  <div class="abs hero"></div>
  <div class="abs hero-photo" role="img" aria-label="Businessman holding a tablet with cloud network icons"></div>
  <div class="hero">
    <h1 class="abs" style="position:absolute">BRISK IT</h1>
  </div>
  <p class="abs hero-sub">That Provides Commercial IT Support &amp; Services</p>
  <p class="abs hero-text">Sed ut perspiciatis unde omnis iste natus error sit voluptatem accusantium doloremque laudantium, totam rem aperiam, eaque ipsa quae ab illo inventore veritatis et quasi architecto beatae vitae dicta sunt explicabo.</p>
  <a class="abs btn-outline">READ MORE</a>
  <div class="abs dots"><span></span><span></span><span class="on"></span><span></span><span></span></div>
</section>

<section class="services">
  <h2 class="abs heading section-title" style="top:384px">OUR SERVICES</h2>
  <p class="abs section-sub" style="top:411px">Sed ut perspiciatis unde omnis iste natus error sit voluptatem accusantium doloremque laudantium, totam rem aperiam, eaque ipsa quae</p>

  <div class="abs service" style="left:57px;top:446px">
    <div class="service-icon"><svg width="30" height="30" viewBox="0 0 30 30" fill="#fff"><ellipse cx="13" cy="6" rx="10" ry="4"/><path d="M3 9c0 2 4.5 4 10 4s10-2 10-4v4c0 2-4.5 4-10 4S3 15 3 13z"/><path d="M3 16c0 2 4.5 4 10 4 1 0 2 0 3-.2V24c-1 .1-2 .2-3 .2-5.5 0-10-2-10-4z"/><circle cx="23" cy="22" r="4.5"/><circle cx="23" cy="22" r="1.8" fill="#1b6cb4"/></svg></div>
    <h3 class="heading">DATA</h3>
    <p class="body-text">Sed ut perspiciatis unde omnis iste natus error sit voluptatem accusantium doloremque laudantium, beatae vitae dicta sunt explicabo.</p>
  </div>
  <div class="abs service" style="left:252px;top:446px">
    <div class="service-icon"><svg width="32" height="30" viewBox="0 0 32 30" fill="none" stroke="#fff" stroke-width="2"><path d="M9 20H7a5 5 0 0 1 0-10 8 8 0 0 1 15-2 6 6 0 0 1 3 12h-2"/><path d="M16 13v13M12 22l4 4 4-4"/></svg></div>
    <h3 class="heading">CLOUD</h3>
    <p class="body-text">Sed ut perspiciatis unde omnis iste natus error sit voluptatem accusantium doloremque laudantium, beatae vitae dicta sunt explicabo.</p>
  </div>
  <div class="abs service" style="left:447px;top:446px">
    <div class="service-icon"><svg width="24" height="30" viewBox="0 0 24 30"><rect x="7" y="2" width="10" height="17" rx="5" fill="#fff"/><path d="M3 14a9 9 0 0 0 18 0M12 23v5M7 28h10" stroke="#fff" stroke-width="2" fill="none"/></svg></div>
    <h3 class="heading">VOICE</h3>
    <p class="body-text">Sed ut perspiciatis unde omnis iste natus error sit voluptatem accusantium doloremque laudantium, beatae vitae dicta sunt explicabo.</p>
  </div>
</section>

<section class="why">
  <div class="abs why-bg"></div>
  <div class="abs why-photo" role="img" aria-label="Support team wearing headsets at computers, one giving a thumbs up"></div>
  <h2 class="abs heading" style="left:48px;top:621px;font-size:13px">WHY BRISK IT</h2>
  <p class="abs body-text" style="left:48px;top:649px;width:286px">Sed ut perspiciatis unde omnis iste natus error sit voluptatem accusantium doloremque laudantium, totam rem aperiam, eaque ipsa quae ab illo inventore veritatis et quasi architecto beatae vitae dicta sunt explicabo. Nemo enim ipsam voluptatem quia voluptas sit aspernatur aut odit aut magni dolores eos qui ratione voluptatem sequi nesciunt.</p>
  <p class="abs body-text" style="left:48px;top:719px;width:286px">Sed ut perspiciatis unde omnis iste natus error sit voluptatem accusantium doloremque laudantium, totam rem aperiam, eaque ipsa quae ab illo inventore veritatis et quasi architecto beatae magni dolores eos qui ratione voluptatem sequi nesciunt.</p>
  <a class="abs btn-solid">READ MORE</a>
</section>

<section class="testimonials">
  <h2 class="abs heading section-title" style="top:844px">OUR TESTIMONIALS</h2>
  <p class="abs section-sub" style="top:870px">Sed ut perspiciatis unde omnis iste natus error sit voluptatem accusantium doloremque laudantium, totam rem aperiam, eaque ipsa quae</p>

  <div class="abs testimonial" style="left:49px;top:905px">
    <div class="avatar" role="img" aria-label="Customer portrait"></div>
    <p class="quote"><b>“</b>Sed ut perspiciatis unde omnis iste natus error sit voluptatem accusantium doloremque laudantium, totam rem vitae dicta sunt explicabo.</p>
    <span class="t-name">DANA REYES</span><span class="t-date">POSTED ON 25 JULY 2017</span><span class="stars">☆☆☆☆★</span>
  </div>
  <div class="abs testimonial" style="left:245px;top:905px">
    <div class="avatar" role="img" aria-label="Customer portrait"></div>
    <p class="quote"><b>“</b>Sed ut perspiciatis unde omnis iste natus error sit voluptatem accusantium doloremque laudantium, totam rem vitae dicta sunt explicabo.</p>
    <span class="t-name">DANA REYES</span><span class="t-date">POSTED ON 25 JULY 2017</span><span class="stars">☆☆☆☆★</span>
  </div>
  <div class="abs testimonial" style="left:441px;top:905px">
    <div class="avatar" role="img" aria-label="Customer portrait"></div>
    <p class="quote"><b>“</b>Sed ut perspiciatis unde omnis iste natus error sit voluptatem accusantium doloremque laudantium, totam rem vitae dicta sunt explicabo.</p>
    <span class="t-name">DANA REYES</span><span class="t-date">POSTED ON 25 JULY 2017</span><span class="stars">☆☆☆☆★</span>
  </div>
</section>

<footer>
  <div class="abs footer"></div>
  <div class="abs logo footer" style="left:48px;top:1090px;width:auto;height:auto;background:none"><span class="logo-dot"></span><span class="logo-name">Brisk IT</span></div>

  <h4 class="abs f-title" style="left:220px;top:1054px">CONTACT US</h4>
  <table class="abs f-list" style="left:220px;top:1075px;border-collapse:collapse">
    <tr><td>Main Number</td><td>:</td><td>555-010-4400</td></tr>
    <tr><td>Houston</td><td>:</td><td>555-014-2200</td></tr>
    <tr><td>San Antonio</td><td>:</td><td>555-017-3300</td></tr>
    <tr><td>Austin</td><td>:</td><td>555-019-5500</td></tr>
    <tr><td>Tulsa</td><td>:</td><td>555-012-6600</td></tr>
    <tr><td>Oklahoma City</td><td>:</td><td>555-016-7700</td></tr>
  </table>

  <h4 class="abs f-title" style="left:358px;top:1054px">NEWSLETTER</h4>
  <p class="abs f-list" style="left:358px;top:1076px;width:120px">Register Your email address to get information about us</p>
  <div class="abs input">Email Address</div>
  <a class="abs subscribe">SUBSCRIBE</a>

  <h4 class="abs f-title" style="left:508px;top:1055px">FOLLOW US</h4>
  <p class="abs f-list" style="left:508px;top:1079px;width:118px;line-height:10.5px">Lorem ipsum dolor sit amet, conse ctetur adipiscing elit. Nulla in purus nibh. Donec ornare</p>
  <div class="abs social"><span></span><span></span><span></span><span></span><span></span></div>

  <div class="abs copyright">© Copyright 2017 Brisk .All Rights Reserved</div>
</footer>

</body>
</html>
```